Simplified minimalist but bold website

Design a website for a brand 'Brighten Every Day' that shares ideas to make managing home and health easier through email swap series, webinars and eventually courses.

Simple landing page to attract users to sign up for a freebie.

Target Market(s)

women with families & homes to run

Number of Pages Required

1 page

Font styles to use
Sans Serif

Colors
e667a6
b768aa
acd136
ffffff
959595

Requirements
Must have
• Simplified look, line icons, opt-in template, contact us form

```html
<!DOCTYPE html>
<html lang="en">
<head>
<meta charset="utf-8">
<title>Brighten Every Day</title>
<link rel="stylesheet" href="https://fonts.googleapis.com/css2?family=Roboto:wght@400;500;700&display=swap">
<style>
:root{
  --blue:#2f94d2;
  --blue-soft:#4ba7dc;
  --pink:#de4b97;
  --pink-deep:#b9487f;
  --pink-button:#e667a6;
  --green:#acd136;
  --ink:#1f1f1f;
  --grey:#959595;
  --white:#ffffff;
  --black:#000000;
}
*{box-sizing:border-box;margin:0;padding:0}
html,body{width:1200px;height:2270px;overflow:hidden}
body{position:relative;font-family:'Roboto',Arial,sans-serif;color:var(--white);background:var(--white)}
.hero-photo{position:absolute;left:0;top:0;width:1200px;height:720px;
  background:radial-gradient(ellipse 260px 360px at 860px 330px,#b8947c 0%,#8a6a55 40%,rgba(40,28,22,0) 100%),
  linear-gradient(90deg,#140f0c 0%,#2a1f19 45%,#5a4638 75%,#8c7560 100%)}
.bottom-photo{position:absolute;left:0;top:1440px;width:1200px;height:675px;
  background:radial-gradient(ellipse 320px 300px at 560px 260px,#e6e3df 0%,#f3f2ef 60%,#f7f7f5 100%)}
.panels{position:absolute;left:0;top:0}
.nav{position:absolute;left:0;top:0;width:1200px;height:112px}
.brand{position:absolute;left:88px;top:36px;font-weight:700;font-size:32px;color:var(--green)}
.menu{position:absolute;top:46px;list-style:none;font-size:17px}
.menu li{position:absolute;white-space:nowrap}
.menu .current{color:#3aa3e0}
.hero-title{position:absolute;left:78px;width:600px;top:232px;text-align:center;font-weight:500;font-size:64px}
.rule{position:absolute;height:3px;background:var(--green)}
.rule.white{background:var(--white)}
.hero-lead{position:absolute;left:78px;width:600px;top:370px;text-align:center;font-size:29px;line-height:49px}
.col{position:absolute;top:0;text-align:center}
.kicker{position:absolute;width:100%;top:780px;font-size:23px}
.col-title{position:absolute;width:100%;top:818px;font-size:42px;font-weight:500}
.pitch{position:absolute;width:100%;top:906px;font-size:16px;font-weight:700}
.body-text{position:absolute;width:100%;top:943px;font-size:15.5px;line-height:25.5px}
.btn{position:absolute;height:30px;font-size:13px;line-height:30px;text-align:center;border-radius:2px}
.btn.sample{background:var(--green)}
.btn.learn{background:var(--ink)}
.optin{position:absolute;border:1.5px solid rgba(255,255,255,.85)}
.optin.blue{background:var(--blue-soft)}
.optin.pink{background:var(--pink-deep)}
.optin h3{position:absolute;width:100%;top:22px;font-size:27px;font-weight:400;text-align:center}
.field{position:absolute;height:46px;background:var(--white);color:var(--ink);font-size:16px;font-weight:500;line-height:46px;padding-left:12px}
.submit{position:absolute;height:45px;font-size:20px;font-weight:500;line-height:45px;text-align:center}
.submit.pinkbtn{background:var(--pink-button)}
.submit.dark{background:#1c1c1c}
.guide-cover{position:absolute;left:723px;top:912px;width:288px;height:226px;
  background:linear-gradient(135deg,#f4f4f4 0%,#dfe6ea 50%,#f0a050 100%);
  transform:rotate(-4deg);box-shadow:0 6px 14px rgba(0,0,0,.25)}
.series{position:absolute;left:0;width:1200px;top:1580px;text-align:center;color:var(--ink)}
.series h2{font-size:48px;font-weight:500}
.series .copy{position:absolute;width:100%;top:102px;font-size:17.5px;line-height:26px;color:#333}
.series .copy.big{top:230px;font-size:19px;line-height:29px}
.series .copy.jam{top:309px}
.cta{position:absolute;left:492px;top:1983px;width:216px;height:60px;background:var(--blue);color:var(--white);font-size:24px;line-height:60px;text-align:center}
.footer{position:absolute;left:0;top:2115px;width:1200px;height:155px;background:var(--black)}
.footer .brand{top:58px;left:88px}
.social{position:absolute;top:64px;list-style:none}
.social li{position:absolute;width:25px;height:25px;border-radius:5px;background:var(--white)}
.copyright{position:absolute;left:877px;top:69px;font-size:15px}
</style>
</head>
<body>
<div class="hero-photo" role="img" aria-label="Photo of a smiling woman in glasses and a grey sweater in a warm home interior"></div>
<div class="bottom-photo" role="img" aria-label="Faded photo of a woman relaxing at home"></div>

<svg class="panels" width="1200" height="2270" viewBox="0 0 1200 2270" aria-hidden="true">
  <polygon points="0,564 600,711 600,1457 0,1604" fill="var(--blue)"/>
  <polygon points="600,711 1200,564 1200,1604 600,1457" fill="var(--pink)"/>
  <polyline points="0,1604 600,1457 1200,1604" fill="none" stroke="#1a1a1a" stroke-width="1.5"/>
</svg>

<header class="nav">
  <div class="brand">Brighten Every Day</div>
  <ul class="menu">
    <li class="current" style="left:600px">Home</li>
    <li style="left:696px">About us</li>
    <li style="left:812px">Services</li>
    <li style="left:927px">Blog</li>
    <li style="left:1021px">Contact us</li>
  </ul>
</header>

<h1 class="hero-title">Brighten Every Day.</h1>
<div class="rule" style="left:303px;top:335px;width:136px"></div>
<p class="hero-lead">Chances are life is a little overwhelming.<br>Let us help</p>

<section class="col" style="left:0;width:666px">
  <p class="kicker">Baby Steps... (try out a few of our tricks)</p>
  <h2 class="col-title">Swaps Email Series</h2>
  <div class="rule white" style="left:270px;top:881px;width:126px"></div>
  <p class="pitch">Save TIME, MONEY and SANITY with simple product swaps.</p>
  <p class="body-text">Reduce the amount of work it takes to run your home.<br>Swap out existing products for more sustainable ones.<br>Each swap saves you work, clutter, time &amp; money.</p>
  <div class="btn sample" style="left:186px;top:1043px;width:136px">See Sample Swap</div>
  <div class="btn learn" style="left:336px;top:1043px;width:103px">Learn More</div>
</section>

<form class="optin blue" style="left:110px;top:1126px;width:448px;height:263px">
  <h3>Send your ideas my way...</h3>
  <div class="field" style="left:33px;top:77px;width:381px">NAME</div>
  <div class="field" style="left:33px;top:132px;width:381px">EMAIL</div>
  <div class="submit pinkbtn" style="left:33px;top:188px;width:381px">SEND ME THE GUIDE!</div>
</form>

<section class="col" style="left:600px;width:522px">
  <p class="kicker">Big Leap... (I’m ready to roll up my sleeves)</p>
  <h2 class="col-title">Decluttering Guide</h2>
  <div class="rule white" style="left:198px;top:881px;width:126px"></div>
</section>
<div class="guide-cover" role="img" aria-label="Printed decluttering guide brochure pages"></div>

<form class="optin pink" style="left:649px;top:1165px;width:446px;height:222px">
  <div class="field" style="left:33px;top:38px;width:382px">NAME</div>
  <div class="field" style="left:33px;top:93px;width:382px">EMAIL</div>
  <div class="submit dark" style="left:33px;top:149px;width:382px">SIGN ME UP!</div>
</form>

<section class="series">
  <h2>Swaps Email Series</h2>
  <div class="rule" style="left:537px;top:66px;width:126px"></div>
  <p class="copy">Save TIME, MONEY and SANITY with simple product swaps.<br>And reduce the amount of work it takes to run your home.<br>Swap out existing products for more sustainable ones.<br>Each swap save you work, clutter, time &amp; money.</p>
  <p class="copy big">You get an email 2x weekly for 6-12 weeks only Get<br>even more if you feel they are helpful to you</p>
  <p class="copy big jam">Join our monthly SIMPLE SWAP SHARING web jams with other mums<br>and get even more ideas. Better yet, come with great tips of your own to</p>
</section>
<div class="cta">SIGN ME UP!!</div>

<footer class="footer">
  <div class="brand">Brighten Every Day</div>
  <ul class="social">
    <li style="left:528px"></li>
    <li style="left:567px"></li>
    <li style="left:607px"></li>
    <li style="left:646px"></li>
  </ul>
  <p class="copyright">Copyright © 2018. All Rights Reserved</p>
</footer>
</body>
</html>
```